Specialised investor in e-mobility and energy wants business card design

We need a business card design that fits our existing corporate design. <The look and feel must be 'sharp'/'clean', dynamic, communicate momentum, professionalism etc (as one would imagine from a firm in the financial sector). We like the idea of a reverse-side of the card that includes the logo, and the name and contact details on the other. We expect the deliverable to be whatever format might be required to be able to get cards printed directly by a service such as kelmo press. Our website is www.zub.capital

```html
<!DOCTYPE html>
<html lang="en">
<head>
<meta charset="utf-8">
<title>Zub Capital – Business Card</title>
<link rel="stylesheet" href="https://fonts.googleapis.com/css2?family=Roboto:wght@400;500;700&display=swap">
<style>
  :root {
    --backdrop: #d3d4d6;
    --forest: #334f24;
    --leaf: #7ab648;
    --paper: #f6f8f1;
    --white: #ffffff;
  }
  * { box-sizing: border-box; margin: 0; padding: 0; }
  html, body {
    width: 900px;
    height: 1200px;
    overflow: hidden;
    background: var(--backdrop);
    font-family: "Roboto", Arial, sans-serif;
  }
  .card {
    position: absolute;
    left: 165px;
    width: 571px;
    height: 374px;
  }
  .card--front {
    top: 190px;
    background: var(--forest);
    display: flex;
    align-items: center;
    justify-content: center;
  }
  .card--back {
    top: 636px;
    background: var(--paper);
  }
  .wordmark {
    font-family: "Roboto", Arial, sans-serif;
    font-weight: 400;
    letter-spacing: 0.5px;
    white-space: nowrap;
  }
  .card--front .wordmark {
    color: var(--white);
    font-size: 50px;
  }
  .card--back .wordmark {
    position: absolute;
    top: 36px;
    right: 33px;
    color: var(--forest);
    font-size: 42px;
  }
  .holder {
    position: absolute;
    left: 33px;
    top: 210px;
  }
  .holder__name {
    color: var(--leaf);
    font-size: 22px;
    font-weight: 700;
    line-height: 1.1;
  }
  .holder__role {
    color: var(--forest);
    font-size: 13.5px;
    margin-top: 5px;
    letter-spacing: 0.3px;
  }
  .holder__rule {
    width: 48px;
    height: 3px;
    background: var(--leaf);
    margin-top: 7px;
  }
  .contact {
    list-style: none;
    margin-top: 14px;
  }
  .contact__item {
    display: flex;
    align-items: center;
    gap: 6px;
    color: var(--forest);
    font-size: 13.5px;
    letter-spacing: 0.5px;
    height: 22px;
  }
  .contact__icon {
    width: 12px;
    height: 12px;
    fill: var(--leaf);
    flex: none;
  }
</style>
</head>
<body>
  <section class="card card--front" aria-label="Card front">
    <span class="wordmark">Zub Capital</span>
  </section>

  <section class="card card--back" aria-label="Card back">
    <span class="wordmark">Zub Capital</span>
    <div class="holder">
      <p class="holder__name">Marten Ollis</p>
      <p class="holder__role">Partner</p>
      <div class="holder__rule"></div>
      <ul class="contact">
        <li class="contact__item">
          <svg class="contact__icon" viewBox="0 0 24 24" aria-hidden="true"><path d="M6.6 10.8c1.4 2.8 3.8 5.1 6.6 6.6l2.2-2.2c.3-.3.7-.4 1-.2 1.1.4 2.3.6 3.6.6.6 0 1 .4 1 1V20c0 .6-.4 1-1 1C10.6 21 3 13.4 3 4c0-.6.4-1 1-1h3.5c.6 0 1 .4 1 1 0 1.3.2 2.5.6 3.6.1.3 0 .7-.2 1L6.6 10.8z"/></svg>
          <span>+41 79000 4418</span>
        </li>
        <li class="contact__item">
          <svg class="contact__icon" viewBox="0 0 24 24" aria-hidden="true"><path d="M2 5h20v14H2V5zm2 2v.5l8 5 8-5V7H4zm0 2.8V17h16V9.8l-8 5-8-5z"/></svg>
          <span>marten@zub.capital</span>
        </li>
        <li class="contact__item">
          <svg class="contact__icon" viewBox="0 0 24 24" aria-hidden="true"><path d="M12 2a10 10 0 100 20 10 10 0 000-20zm6.9 6h-2.9a15 15 0 00-1.4-3.6A8 8 0 0118.9 8zM12 4c.8 1.2 1.5 2.5 1.9 4h-3.8c.4-1.5 1.1-2.8 1.9-4zM4.3 14a8 8 0 010-4h3.4a16 16 0 000 4H4.3zm.8 2h2.9c.3 1.3.8 2.5 1.4 3.6A8 8 0 015.1 16zM8 8H5.1a8 8 0 014.3-3.6C8.8 5.5 8.3 6.7 8 8zm4 12c-.8-1.2-1.5-2.5-1.9-4h3.8c-.4 1.5-1.1 2.8-1.9 4zm2.3-6H9.7a14 14 0 010-4h4.6a14 14 0 010 4zm.3 5.6c.6-1.1 1.1-2.3 1.4-3.6h2.9a8 8 0 01-4.3 3.6zm1.7-5.6a16 16 0 000-4h3.4a8 8 0 010 4h-3.4z"/></svg>
          <span>www.zub.capital</span>
        </li>
      </ul>
    </div>
  </section>
</body>
</html>
```